Commercial/Corporate Law Firm needs Website Design

Hi guys. I've started up a new law firm and would love your help designing an attractive website. I'll need both design and coding, and to make it easy for us to edit as necessary later, I think it should be built off a Wordpress.org structure.
FIRST IMPRESSIONS
It's very important that the first impression of the website really captures our prospective clients' attention and impresses them. Their first three seconds needs to be good.
I imagine the homepage may be short, with a menu bar and a compelling image, and with a tagline overlaid or underneath (eg. "It's about results.")
The image should be related to our practice areas: eg. IPOs, corporate transactions, or commercial negotiations.
I have previously suggested there could be a skyline image of Sydney or Adelaide. However, because we are based in Adelaide, I don't think Sydney is appropriate - and Adelaide is probably too boring to use.
HOMEPAGE
Being a new firm, we don't have many existing testimonials, and I will be the only lawyer to start with. So we need to focus on the nature of the services we will provide and how my experience can help them. We have an existing logo to use, and I would like the website colour scheme not to clash with that logo (dark blue and white).
After the initial image and tagline there should be a brief introduction to each of the main areas of work, eg. "We specialise in three main areas of practice:"
1. Corporate Transactions and Regulation
2. Business Law and Dispute Resolution
3. Migration Assistance
These should each have an appropriate photo and link to a separate page that briefly describes our services in that area.
Below that there should be a message from me with a photo. Finally, at the bottom, there should be a "Contact Us" section which shows a Google image of our address, contact details, and then our logo with colours inverted.
OTHER PAGES
While we will need some other pages, they should all be fairly simple. I think we will need one page to say "About Us", where I will put information about my experience. I think we will then need one page for each of the 3 areas listed above, which just needs an appropriate image and then text to describe the service. Finally, a "Contact Us" page which I imagine will be the same as the bottom of the homepage.
OTHER DETAILS
For now you can use details from my plain square page to fill out any other text as necessary, or the photo.
Because the logo is square, I would prefer the design of the website also to be rectangular.
Looking forward to seeing your work! Thank you.
Marcus
Potential clients:
Businesses with legal issues or disputes
Companies wishing to list on the stock market

```html
<!DOCTYPE html>
<html lang="en">
<head>
<meta charset="utf-8">
<title>Corvane Legal</title>
<link href="https://fonts.googleapis.com/css2?family=Cinzel:wght@400;600&family=Lato:wght@400;700&family=Arimo:wght@400;700&display=swap" rel="stylesheet">
<style>
:root{
  --navy:#1c3666;
  --navy-deep:#12264b;
  --night:#0c1628;
  --ink:#222;
  --muted:#6b6b6b;
  --soft:#efefef;
  --field:#ececec;
  --white:#fff;
  --footer-text:#b9c2d3;
}
*{box-sizing:border-box;margin:0;padding:0}
html,body{width:1200px;height:2913px;overflow:hidden;background:var(--white)}
body{position:relative;font-family:"Arimo",Arial,sans-serif;color:var(--ink)}
.abs{position:absolute}
.serif{font-family:"Cinzel",Georgia,serif}

/* hero */
.hero{left:0;top:0;width:1200px;height:676px;background:linear-gradient(180deg,#0d1a35 0%,#1a3466 45%,#101d38 75%,#081020 100%)}
.hero-photo{left:0;top:74px;width:1200px;height:602px;background:radial-gradient(ellipse at 30% 85%,rgba(120,160,230,.35),transparent 55%),linear-gradient(180deg,#14284f 0%,#1f3b70 55%,#0a1428 100%)}
.hero-person{left:660px;top:96px;width:460px;height:580px;background:linear-gradient(180deg,#2b2b38 0%,#1d1d28 100%);border-radius:200px 200px 0 0}
.topbar{left:0;top:0;width:1200px;height:74px;background:rgba(8,16,34,.75)}
.brand{left:78px;top:0;width:192px;height:142px;background:var(--white);display:flex;flex-direction:column;align-items:center;justify-content:center;gap:10px}
.brand .mark{width:44px;height:44px;background:var(--navy)}
.brand .name{font-family:"Cinzel",Georgia,serif;color:var(--navy);font-size:21px;letter-spacing:2px;text-align:center;line-height:1.1}
.nav{left:460px;top:26px;display:flex;gap:26px;font-size:15px;color:var(--white);text-transform:uppercase}
.nav li{list-style:none;display:flex;align-items:center;gap:8px}
.nav .active::before{content:"";width:9px;height:9px;background:var(--white);display:inline-block}
.search{left:903px;top:14px;width:219px;height:46px;border:1px solid rgba(255,255,255,.35);display:flex;align-items:center;padding:0 14px;color:#8a93a6;font-size:14px;justify-content:space-between}
.hero-title{left:78px;top:366px;font-family:"Lato",sans-serif;font-weight:700;font-size:58px;color:var(--white)}
.hero-copy{left:78px;top:440px;width:460px;font-size:15px;font-weight:700;line-height:23px;color:var(--white)}
.dots{left:548px;top:640px;display:flex;gap:9px}
.dots span{width:15px;height:15px;border:2px solid var(--white);border-radius:50%}

/* shared */
.heading{font-family:"Cinzel",Georgia,serif;color:var(--navy);font-size:46px;font-weight:600;letter-spacing:1px;text-align:center;width:1200px;left:0}
.tagline{left:0;width:1200px;display:flex;justify-content:center;align-items:center;gap:18px;font-size:18px;letter-spacing:2px;color:#555;text-transform:uppercase}
.tagline::before,.tagline::after{content:"";width:64px;height:1px;background:#555}
.btn{background:var(--navy);color:var(--white);font-family:"Cinzel",Georgia,serif;font-size:21px;letter-spacing:1px;display:flex;align-items:center;justify-content:center}

/* welcome */
.welcome-copy{left:180px;top:832px;width:840px;text-align:center;font-size:14.5px;line-height:28px;color:var(--muted)}
.welcome-copy p+p{margin-top:8px}

/* practice */
.practice{left:0;top:1103px;width:1200px;height:596px;background:linear-gradient(180deg,#1d3566 0%,#263f70 40%,#1a2f5a 100%)}
.practice .heading{color:var(--white);top:56px}
.practice .tagline{top:118px;color:#b8c2d6}
.practice .tagline::before,.practice .tagline::after{background:#b8c2d6;width:70px}
.card{top:183px;width:324px;height:352px;background:var(--white)}
.card .pic{height:186px}
.card h3{font-family:"Cinzel",Georgia,serif;color:var(--navy);font-weight:400;font-size:19px;line-height:27px;text-align:center;margin-top:18px;padding:0 16px}
.card p{font-size:14px;line-height:23px;color:var(--muted);text-align:center;margin-top:12px;padding:0 26px}
.card.current::after{content:"";position:absolute;left:150px;bottom:-12px;border:12px solid transparent;border-top-color:var(--white);border-bottom:0}

/* about */
.about{left:0;top:1699px;width:1200px;height:395px;background:var(--soft)}
.about-person{left:163px;top:39px;width:303px;height:356px;background:linear-gradient(180deg,#3a3444 0%,#24212d 100%);border-radius:140px 140px 0 0}
.about h2{left:569px;top:58px;font-family:"Cinzel",Georgia,serif;color:var(--navy);font-size:44px;font-weight:600}
.about-copy{left:569px;top:124px;width:540px;font-size:14.5px;line-height:27px;color:var(--muted)}
.about-copy p+p{margin-top:14px}

/* contact */
.contact-lead{left:0;top:2246px;width:1200px;text-align:center;font-weight:700;font-size:16px}
.field{height:47px;background:var(--field);font-size:14px;color:#555;padding:0 12px;display:flex;align-items:center}
.field.focus{background:var(--white);border:1.5px solid var(--navy);color:var(--ink)}
.field.area{align-items:flex-start;padding-top:14px}

/* footer */
.footer{left:0;top:2583px;width:1200px;height:266px;background:linear-gradient(180deg,#0b1424,#0e1a30)}
.foot-brand{left:78px;top:30px;width:223px;display:flex;flex-direction:column;align-items:center;gap:12px}
.foot-brand .mark{width:70px;height:70px;border:2px solid #2d4a80}
.foot-brand .name{font-family:"Cinzel",Georgia,serif;color:#2d4a80;font-size:30px;letter-spacing:3px;text-align:center;line-height:1.1}
.social{left:175px;top:184px;width:39px;height:39px;background:var(--navy)}
.foot-col h4{font-family:"Cinzel",Georgia,serif;color:var(--white);font-weight:400;font-size:17px;letter-spacing:1px;margin-bottom:22px}
.foot-col li{list-style:none;color:var(--footer-text);font-size:14px;line-height:21px;margin-bottom:8px;display:flex;gap:14px}
.foot-col li::before{content:"";width:7px;height:7px;background:var(--navy);margin-top:7px;flex:none}
.foot-contact li::before{display:none}
.foot-contact svg{flex:none}
.copyright{left:0;top:2849px;width:1200px;height:64px;background:var(--navy);color:#dfe5f0;font-size:14px;display:flex;align-items:center;justify-content:center}
</style>
</head>
<body>

<header>
  <div class="abs hero"></div>
  <div class="abs hero-photo" role="img" aria-label="City skyline at night with lit skyscrapers along the waterfront"></div>
  <div class="abs hero-person" role="img" aria-label="Smiling lawyer in dark suit and red tie"></div>
  <div class="abs topbar"></div>
  <div class="abs brand"><span class="mark"></span><span class="name">Corvane<br>Legal</span></div>
  <ul class="abs nav">
    <li class="active">Home</li><li>About</li><li>Practice Areas</li><li>Contact Us</li>
  </ul>
  <div class="abs search">Search...
    <svg width="18" height="18" viewBox="0 0 18 18"><circle cx="7.5" cy="7.5" r="5.5" fill="none" stroke="#fff" stroke-width="2.4"/><line x1="11.5" y1="11.5" x2="16.5" y2="16.5" stroke="#fff" stroke-width="2.6"/></svg>
  </div>
  <h1 class="abs hero-title">We Get Results</h1>
  <p class="abs hero-copy">Lorem Ipsum is simply dummy text of the printing and type setting industry Lorem Ipsum has.</p>
  <div class="abs dots"><span></span><span></span><span></span><span></span><span></span></div>
</header>

<section>
  <h2 class="abs heading" style="top:732px">Welcome to Corvane</h2>
  <div class="abs tagline" style="top:794px">Legal</div>
  <div class="abs welcome-copy">
    <p>Lorem Ipsum is simply dummy text of the printing and typesetting industry. Lorem Ipsum has been the industry's standard dummy text ever since the 1500s, when an unknown printer took a galley of type and scrambled.</p>
    <p>Lorem Ipsum is simply dummy text of the printing and typesetting industry. Lorem Ipsum has been the industry's standard dummy text ever since the 1500s, when an unknown printer took a galley of type and scrambled it to make a type specimen book. It has survived not only five centuries, but also the leap into electronic typesetting</p>
  </div>
  <a class="abs btn" style="left:507px;top:988px;width:186px;height:51px">Learn More</a>
</section>

<section class="abs practice">
  <h2 class="abs heading">Practice Areas</h2>
  <div class="abs tagline">We specialise in three main areas of practice</div>
  <article class="abs card" style="left:78px">
    <div class="pic" role="img" aria-label="Two business people shaking hands" style="background:linear-gradient(135deg,#5e6f86,#c9cfd8 55%,#8a95a6)"></div>
    <h3>Corporate Transactions<br>and Regulation</h3>
    <p>Lorem Ipsum is simply dummy text of the printing and typesetting industry.</p>
  </article>
  <article class="abs card current" style="left:439px">
    <div class="pic" role="img" aria-label="Hands passing a document across a desk" style="background:linear-gradient(135deg,#d7dde3,#f2f4f6 50%,#5a6472)"></div>
    <h3>Business Law and Dispute<br>Resolution</h3>
    <p>Lorem Ipsum is simply dummy text of the printing and typesetting industry.</p>
  </article>
  <article class="abs card" style="left:800px">
    <div class="pic" role="img" aria-label="Immigration law book with glasses on a wooden desk" style="background:linear-gradient(135deg,#8a4a2a,#e9e3d6 50%,#6b3b22)"></div>
    <h3>Migration<br>Assistance</h3>
    <p>Lorem Ipsum is simply dummy text of the printing and typesetting industry.</p>
  </article>
</section>

<section class="abs about">
  <div class="abs about-person" role="img" aria-label="Portrait of the firm's lawyer in a dark suit"></div>
  <h2 class="abs">About Us</h2>
  <div class="abs about-copy">
    <p>Lorem Ipsum is simply dummy text of the printing and typesetting industry. Lorem Ipsum has been the industry's standard dummy text ever.</p>
    <p>Lorem Ipsum is simply dummy text of the printing and typesetting industry. Lorem Ipsum has been the industry's standard dummy text ever since the 1500s, when an unknown printer took a galley of type and scrambled.</p>
  </div>
  <a class="abs btn" style="left:569px;top:282px;width:177px;height:50px">Learn More</a>
</section>

<section>
  <h2 class="abs heading" style="top:2148px">Contcat Us</h2>
  <div class="abs tagline" style="top:2210px">Keep in Touch</div>
  <p class="abs contact-lead">Need An Have Question Please Contact Us Today.</p>
  <div class="abs field focus" style="left:150px;top:2297px;width:291px">Name *</div>
  <div class="abs field" style="left:454px;top:2297px;width:290px">Email *</div>
  <div class="abs field" style="left:755px;top:2297px;width:292px">Phone *</div>
  <div class="abs field area" style="left:150px;top:2356px;width:897px;height:101px">Message *</div>
  <a class="abs btn" style="left:511px;top:2470px;width:176px;height:51px">Submit</a>
</section>

<footer>
  <div class="abs footer">
    <div class="abs foot-brand"><span class="mark"></span><span class="name">Corvane<br>Legal</span></div>
    <div class="abs social"></div>
    <div class="abs foot-col" style="left:344px;top:34px">
      <h4>Sitemap</h4>
      <ul><li>Home</li><li>About</li><li>Practice Areas</li><li>Contact</li></ul>
    </div>
    <div class="abs foot-col" style="left:612px;top:34px;width:220px">
      <h4>Practice Areas</h4>
      <ul><li>Corporate Transactions &amp; Regulation</li><li>Business Law And Dispute Resolution</li><li>Migration Assistance</li></ul>
    </div>
    <div class="abs foot-col foot-contact" style="left:878px;top:34px;width:250px">
      <h4>Contact Us</h4>
      <ul>
        <li><svg width="18" height="24" viewBox="0 0 18 24"><path d="M9 0a9 9 0 0 0-9 9c0 7 9 15 9 15s9-8 9-15a9 9 0 0 0-9-9z" fill="#2f5291"/><circle cx="9" cy="9" r="3.4" fill="#0d1829"/></svg>101 - Lorem is the simple text print and type text.</li>
        <li><svg width="18" height="18" viewBox="0 0 24 24"><path d="M6.6 10.8a15 15 0 0 0 6.6 6.6l2.2-2.2a1 1 0 0 1 1-.25 11.4 11.4 0 0 0 3.6.57 1 1 0 0 1 1 1V20a1 1 0 0 1-1 1A17 17 0 0 1 3 4a1 1 0 0 1 1-1h3.5a1 1 0 0 1 1 1c0 1.25.2 2.45.57 3.57a1 1 0 0 1-.25 1z" fill="#2f5291"/></svg>123 456 7890</li>
        <li><svg width="18" height="14" viewBox="0 0 18 14"><rect width="18" height="14" fill="#2f5291"/><path d="M0 0l9 7 9-7" fill="none" stroke="#0d1829" stroke-width="1.6"/></svg>info@corvanelegal.com</li>
      </ul>
    </div>
  </div>
  <div class="abs copyright">©CORVANE LEGAL - 2018 All Right Reserved.</div>
</footer>

</body>
</html>
```